Mobile Fitness snd Therapy Business Card Design

I need a business card designed for my mobile fitness and therapy business.

Please view the images that I have uploaded. I like the simplicity of the design that I have attached. I adapted it with my information

Target Market(s)

Those seeking personal training, injury rehabilitation or massage therapy.

Industry/Entity Type

Business

Contact Information for Business Card

Derek Fulham - BSC, CPT, LMT, CES, NC1
e-mail: derek@vantrelo.com
website: www.vantrelo.com
instagram: @derek_fulham

Font styles to use
Sans Serif

Colors
3176b5
0355a3

Requirements
Must have
• "Contact us to receive a FREE assessment"
• Services offered:
• Personal Training
• Golf Fitness
• Injury Rehab
• Massage Therapy
• Yoga
Nice to have
• Consistent colours with brand
• - Dark Blue: #232837
• - Blue: #5096f0
• Consistent look/feel with the website: www.vantrelo.com

```html
<!DOCTYPE html>
<html lang="en">
<head>
<meta charset="utf-8">
<title>Vantrelo Business Card</title>
<link href="https://fonts.googleapis.com/css2?family=Roboto:wght@400;500;700&family=Roboto+Condensed:wght@400;700&display=swap" rel="stylesheet">
<style>
  :root {
    --navy: #232837;
    --blue: #5096f0;
    --blue-deep: #0355a3;
    --blue-mid: #3176b5;
    --paper: #f6f6f6;
    --grey-text: #555b66;
    --backdrop: #e9e6e1;
  }
  * { margin: 0; padding: 0; box-sizing: border-box; }
  html, body { width: 1200px; height: 886px; overflow: hidden; }
  body {
    background: var(--backdrop);
    font-family: "Roboto", Arial, sans-serif;
    position: relative;
  }
  .card {
    position: absolute;
    left: 320px;
    width: 560px;
    height: 320px;
    border-radius: 22px;
    box-shadow: 0 6px 18px rgba(0,0,0,0.18);
    overflow: hidden;
  }
  .card-front { top: 88px; background: var(--navy); }
  .card-back { top: 478px; background: var(--paper); }

  .brand { display: flex; flex-direction: column; align-items: flex-start; }
  .brand-name {
    display: flex; align-items: center; gap: 12px;
    font-weight: 700;
    letter-spacing: 6px;
    line-height: 1;
  }
  .brand-mark { display: inline-block; }
  .brand-tagline {
    font-weight: 700;
    letter-spacing: 3px;
    margin-top: 8px;
  }

  .card-front .brand {
    position: absolute; left: 50%; top: 50%;
    transform: translate(-50%, -50%);
  }
  .card-front .brand-name { color: #ffffff; font-size: 52px; }
  .card-front .brand-mark { width: 14px; height: 14px; background: var(--blue); }
  .card-front .brand-tagline { color: #ffffff; font-size: 14px; padding-left: 26px; }

  .edge-tab {
    position: absolute; width: 12px; height: 82px; background: var(--navy);
  }
  .edge-tab.left { left: 0; top: 195px; border-radius: 0 8px 8px 0; }
  .edge-tab.right { right: 0; top: 40px; border-radius: 8px 0 0 8px; }

  .card-back .brand { position: absolute; left: 44px; top: 118px; }
  .card-back .brand-name { color: var(--navy); font-size: 40px; letter-spacing: 5px; }
  .card-back .brand-mark { width: 11px; height: 11px; background: var(--blue); }
  .card-back .brand-tagline { color: var(--navy); font-size: 11px; letter-spacing: 2.5px; }

  .contact-block { position: absolute; left: 340px; top: 36px; }
  .person-name {
    font-family: "Roboto Condensed", Arial, sans-serif;
    font-weight: 700; font-size: 24px; color: var(--blue);
    line-height: 1;
  }
  .person-credentials {
    font-family: "Roboto Condensed", Arial, sans-serif;
    font-weight: 700; font-size: 10px; color: var(--blue-mid);
    margin-top: 3px; margin-bottom: 14px;
  }
  .contact-list { list-style: none; }
  .contact-list li {
    display: flex; align-items: center; gap: 8px;
    font-size: 13px; color: var(--grey-text); margin-bottom: 5px;
  }
  .contact-icon { width: 13px; height: 13px; flex: none; }

  .offer {
    position: absolute; left: 0; right: 0; top: 236px;
    text-align: center; color: var(--blue);
    font-weight: 700; font-size: 14px;
  }
  .services {
    position: absolute; left: 0; right: 0; top: 262px;
    text-align: center; color: var(--grey-text); font-size: 14px;
  }
  .services .sep { color: var(--blue); padding: 0 3px; }
</style>
</head>
<body>

<section class="card card-front" aria-label="Card front">
  <div class="brand">
    <div class="brand-name">VANTRELO <span class="brand-mark"></span></div>
    <div class="brand-tagline">MOVE - RECOVER - THRIVE</div>
  </div>
</section>

<section class="card card-back" aria-label="Card back">
  <span class="edge-tab left"></span>
  <span class="edge-tab right"></span>

  <div class="brand">
    <div class="brand-name">VANTRELO <span class="brand-mark"></span></div>
    <div class="brand-tagline">MOVE - RECOVER - THRIVE</div>
  </div>

  <div class="contact-block">
    <div class="person-name">DEREK FULHAM</div>
    <div class="person-credentials">BSC, CPT, LMT, CES, NC1</div>
    <ul class="contact-list">
      <li>
        <svg class="contact-icon" viewBox="0 0 16 16"><circle cx="8" cy="8" r="8" fill="#0355a3"/><rect x="3.5" y="5" width="9" height="6" rx="1" fill="#fff"/><path d="M3.8 5.4 8 8.6l4.2-3.2" fill="none" stroke="#0355a3" stroke-width="1"/></svg>
        derek@vantrelo.com
      </li>
      <li>
        <svg class="contact-icon" viewBox="0 0 16 16"><circle cx="8" cy="8" r="8" fill="#0355a3"/><circle cx="8" cy="8" r="4.5" fill="none" stroke="#fff" stroke-width="1.1"/><path d="M3.5 8h9M8 3.5c-2 2.5-2 6.5 0 9M8 3.5c2 2.5 2 6.5 0 9" fill="none" stroke="#fff" stroke-width="0.9"/></svg>
        www.vantrelo.com
      </li>
      <li>
        <svg class="contact-icon" viewBox="0 0 16 16"><circle cx="8" cy="8" r="8" fill="#0355a3"/><circle cx="8" cy="8" r="3" fill="#fff"/></svg>
        @derek_fulham
      </li>
    </ul>
  </div>

  <p class="offer">Contact us to receive a FREE assessment</p>
  <p class="services">Personal Training<span class="sep">|</span>Golf Fitness<span class="sep">|</span>Injury Rehab<span class="sep">|</span>Massage Therapy<span class="sep">|</span>Yoga</p>
</section>

</body>
</html>
```